Design a New Business Card for Our Company

We are looking for fresh, unique, and a modern business card that reflects our roots as digital marketing agency focused on SEM.

Industry/Entity Type

Marketing

Contact Information for Business Card

looking for very unique out of the box designs. clean and modern that compliments our logo

Requirements
Must have
• colors should match our logo
• Front should have name, address, email, and phone/fax of the person, phone/fax are the same number
• back should have our url

```html
<!DOCTYPE html>
<html lang="en">
<head>
<meta charset="utf-8">
<title>Clearvane Media – Business Card</title>
<link href="https://fonts.googleapis.com/css2?family=Arimo:wght@400;700&display=swap" rel="stylesheet">
<style>
  :root {
    --page: #ece9e4;
    --card: #f7f7f7;
    --blue: #6aa8d2;
    --blue-deep: #4a87bd;
    --blue-text: #4a8fc8;
    --grey: #c4c4c4;
    --grey-text: #9a9a9a;
    --ink: #8c8c8c;
    --white: #ffffff;
  }
  * { margin: 0; padding: 0; box-sizing: border-box; }
  html, body { width: 1200px; height: 780px; overflow: hidden; }
  body {
    background: var(--page);
    font-family: "Arimo", Arial, sans-serif;
    position: relative;
  }
  .card {
    position: absolute;
    width: 560px;
    height: 320px;
    border-radius: 14px;
    background: var(--card);
    overflow: hidden;
    box-shadow: 0 6px 18px rgba(0,0,0,.18);
    top: 230px;
  }
  .card--front { left: 30px; }
  .card--back { left: 610px; }
  .card svg.bands { position: absolute; inset: 0; }
  .brand {
    position: absolute;
    display: flex;
    align-items: center;
    gap: 10px;
    color: var(--grey-text);
    font-weight: 700;
    font-size: 34px;
    letter-spacing: -0.5px;
  }
  .brand__dot {
    width: 22px; height: 22px; border-radius: 50%;
    background: var(--blue-text);
  }
  .card--front .brand { left: 40px; top: 118px; }
  .person { position: absolute; right: 34px; top: 26px; text-align: right; }
  .person__name { color: var(--blue-text); font-weight: 700; font-size: 15px; letter-spacing: .5px; }
  .person__title { color: var(--grey-text); font-size: 11px; margin-top: 2px; }
  .lines-right { position: absolute; right: 34px; top: 82px; }
  .lines-left { position: absolute; left: 40px; top: 196px; }
  .contact-line {
    display: flex; align-items: center; gap: 7px;
    color: var(--ink); font-size: 12px; line-height: 19px;
  }
  .lines-right .contact-line { flex-direction: row-reverse; }
  .icon { width: 14px; height: 14px; display: block; }
  .address {
    position: absolute; right: 26px; bottom: 34px;
    color: var(--white); font-size: 12.5px; line-height: 17px;
    text-align: right;
    transform: rotate(-17deg); transform-origin: right bottom;
  }
  .card--back .brand { left: 50%; top: 132px; transform: translateX(-50%); white-space: nowrap; }
  .website {
    position: absolute; left: 62px; bottom: 26px;
    color: var(--white); font-size: 13px;
    transform: rotate(-10deg); transform-origin: left bottom;
  }
</style>
</head>
<body>

<svg width="0" height="0" style="position:absolute">
  <defs>
    <linearGradient id="band-blue" x1="0" y1="0" x2="1" y2="1">
      <stop offset="0" stop-color="#7fb8dd"/>
      <stop offset="1" stop-color="#4a87bd"/>
    </linearGradient>
    <symbol id="icon-phone" viewBox="0 0 14 14">
      <rect width="14" height="14" rx="2" fill="#4a8fc8"/>
      <path d="M4 3.2c.6-.4 1.2.9 1.4 1.5.2.5-.6.8-.4 1.4.4 1 1 1.6 2 2 .6.2.9-.6 1.4-.4.6.2 1.9.8 1.5 1.4-.5.9-1.6 1.2-2.6.8C5.4 9.1 4.3 8 3.5 6.2 3.1 5.1 3.2 3.8 4 3.2Z" fill="#fff"/>
    </symbol>
    <symbol id="icon-fax" viewBox="0 0 14 14">
      <rect width="14" height="14" rx="2" fill="#4a8fc8"/>
      <rect x="4" y="2.5" width="6" height="3.5" fill="#fff"/>
      <rect x="2.5" y="6" width="9" height="5" rx="1" fill="#fff"/>
      <rect x="4" y="8" width="6" height="1" fill="#4a8fc8"/>
    </symbol>
    <symbol id="icon-mail" viewBox="0 0 14 14">
      <rect width="14" height="14" rx="2" fill="#4a8fc8"/>
      <rect x="2.5" y="4" width="9" height="6.5" fill="#fff"/>
      <path d="M2.5 4 7 8l4.5-4" fill="none" stroke="#4a8fc8" stroke-width="1"/>
    </symbol>
  </defs>
</svg>

<section class="card card--front" aria-label="Business card front">
  <svg class="bands" viewBox="0 0 560 320" aria-hidden="true">
    <path d="M80 320 C300 286 470 216 560 146 L560 168 C470 234 320 300 170 320 Z" fill="var(--grey)"/>
    <path d="M190 320 C340 300 470 250 560 188 L560 320 Z" fill="url(#band-blue)"/>
  </svg>

  <div class="person">
    <div class="person__name">ELENA MARSH</div>
    <div class="person__title">Manager</div>
  </div>

  <div class="lines-right">
    <div class="contact-line"><svg class="icon"><use href="#icon-phone"/></svg>555 204 1187</div>
    <div class="contact-line"><svg class="icon"><use href="#icon-fax"/></svg>555 204 1187</div>
  </div>

  <div class="brand"><span class="brand__dot"></span>Clearvane Media</div>

  <div class="lines-left">
    <div class="contact-line"><svg class="icon"><use href="#icon-phone"/></svg>555 204 1187</div>
    <div class="contact-line"><svg class="icon"><use href="#icon-fax"/></svg>555 204 1187</div>
    <div class="contact-line"><svg class="icon"><use href="#icon-mail"/></svg>elena@clearvane.com</div>
  </div>

  <div class="address">48 Harbor Row, 2nd Ste<br>Brookdale, Ohio 4521</div>
</section>

<section class="card card--back" aria-label="Business card back">
  <svg class="bands" viewBox="0 0 560 320" aria-hidden="true">
    <path d="M0 0 H560 V34 C380 44 190 74 0 120 Z" fill="url(#band-blue)"/>
    <path d="M0 134 C190 86 380 56 560 48 L560 58 C380 68 200 98 0 150 Z" fill="var(--grey)"/>
    <path d="M0 236 C200 200 380 170 560 140 L560 160 C380 192 200 226 0 262 Z" fill="var(--grey)"/>
    <path d="M0 272 C200 236 380 204 560 172 V320 H0 Z" fill="url(#band-blue)"/>
  </svg>

  <div class="brand"><span class="brand__dot"></span>Clearvane Media</div>

  <div class="website">www.clearvane.com</div>
</section>

</body>
</html>
```